I would like a business card to match my truck wrap and logo. I would like the font to match my existing business card please.

Industry/Entity Type

Painter

Contact Information for Business Card

Rodrigo Fenwar 801-437-2190 Fenwarcoatings.utah@brelmox.com
SERVICES - Custom Paint & Stain, Interior & Exterior, Epoxy Coatings / Garage Floors, Cabinet Refinishing, Log Staining and Refinishing.

Requirements
Nice to have
• I would like to have the white and grey line like the bottom of my vehicle wrap, Light Grey to match my truck also.

```html
<!DOCTYPE html>
<html lang="en">
<head>
<meta charset="utf-8">
<title>Fenwar Painting – Business Card</title>
<link href="https://fonts.googleapis.com/css2?family=Exo+2:wght@700;800&family=Roboto:wght@400;500;700&display=swap" rel="stylesheet">
<style>
  :root {
    --page-bg: #e6e7e9;
    --card-bg: #1c1d1f;
    --card-bg-deep: #151618;
    --brand-blue: #19a6ee;
    --brand-blue-dark: #0b6fb8;
    --text-white: #ffffff;
    --rule-grey: #9a9ca0;
    --pattern-grey: #2a2b2e;
  }
  * { box-sizing: border-box; margin: 0; padding: 0; }
  html, body {
    width: 1200px; height: 1108px; overflow: hidden;
    background: var(--page-bg);
  }
  .sheet {
    width: 1200px; height: 1108px;
    display: flex; align-items: center; justify-content: center; gap: 80px;
  }
  .card {
    position: relative;
    width: 420px; height: 700px;
    background: var(--card-bg);
    border-radius: 26px;
    overflow: hidden;
    box-shadow: 0 18px 40px rgba(0,0,0,.28);
  }

  /* Front */
  .front-brand {
    position: absolute; top: 150px; left: 0; right: 0;
    display: flex; flex-direction: column; align-items: center; gap: 26px;
  }
  .brand-square {
    width: 110px; height: 110px;
    background: linear-gradient(135deg, var(--brand-blue), var(--brand-blue-dark));
    border-radius: 10px;
  }
  .brand-name {
    font-family: "Exo 2", sans-serif; font-weight: 800;
    color: var(--brand-blue);
    font-size: 44px; letter-spacing: 2px; text-transform: uppercase;
    text-align: center; line-height: 1.1;
  }
  .front-contact {
    position: absolute; bottom: 90px; left: 0; right: 0;
    text-align: center;
    font-family: "Exo 2", sans-serif; font-weight: 800;
    color: var(--brand-blue);
  }
  .contact-name { font-size: 30px; text-transform: uppercase; letter-spacing: .5px; }
  .contact-rule {
    width: 130px; height: 1px; background: var(--rule-grey);
    margin: 14px auto 16px;
  }
  .contact-phone { font-size: 26px; margin-bottom: 10px; }
  .contact-email { font-size: 19px; }

  /* Back */
  .back-pattern {
    position: absolute; inset: 0;
    background: linear-gradient(170deg, var(--pattern-grey) 0%, var(--card-bg) 55%, var(--card-bg-deep) 100%);
  }
  .back-mark {
    position: absolute; top: 330px; left: 50%;
    transform: translateX(-50%);
    width: 80px; height: 80px;
    background: linear-gradient(135deg, var(--brand-blue), var(--brand-blue-dark));
    border-radius: 8px;
  }
  .services {
    position: absolute; top: 440px; left: 0; right: 0;
    text-align: center; color: var(--text-white);
    font-family: "Roboto", sans-serif;
  }
  .services-title { font-weight: 700; font-size: 24px; margin-bottom: 6px; }
  .services-list { list-style: none; font-size: 21px; line-height: 1.5; font-weight: 400; }
</style>
</head>
<body>
<main class="sheet">
  <section class="card card-front">
    <div class="front-brand">
      <div class="brand-square"></div>
      <div class="brand-name">Fenwar<br>Painting</div>
    </div>
    <div class="front-contact">
      <p class="contact-name">Rodrigo Fenwar</p>
      <div class="contact-rule"></div>
      <p class="contact-phone">801-437-2190</p>
      <p class="contact-email">Fenwarcoatings.utah@brelmox.com</p>
    </div>
  </section>

  <section class="card card-back">
    <div class="back-pattern" role="img" aria-label="Faint repeating decorative pattern of tiles in dark grey"></div>
    <div class="back-mark"></div>
    <div class="services">
      <h2 class="services-title">SERVICES</h2>
      <ul class="services-list">
        <li>Custom Paint &amp; Stain</li>
        <li>Interior &amp; Exterior</li>
        <li>Epoxy Coatings / Garage Floors</li>
        <li>Cabinet Refinishing</li>
        <li>Log Staining and Refinishing.</li>
      </ul>
    </div>
  </section>
</main>
</body>
</html>
```